business card deign

Logo needs the following on it.
1. attached logo
2. Tagline - "If it keeps a drink cold or the party going...we do it!"
3. Name- Dalton Pikes, Founder and CPO
4. Address - 412 E. Carver Avenue, Ste 2207, Tampa, FL. 33917
5. Phone - 555.318.4726

```html
<!DOCTYPE html>
<html lang="en">
<head>
<meta charset="utf-8">
<title>Wallay Business Card</title>
<link rel="stylesheet" href="https://fonts.googleapis.com/css2?family=Open+Sans:wght@400;700&display=swap">
<style>
  :root{
    --stage:#232323;
    --card-dark:#0d0d0d;
    --pattern-a:#1c1c1c;
    --pattern-b:#2a2a2a;
    --card-light:#ffffff;
    --ink:#111111;
    --faint:#e6e6e6;
    --white:#ffffff;
  }
  *{margin:0;padding:0;box-sizing:border-box}
  html,body{width:1200px;height:780px;overflow:hidden;background:var(--stage);font-family:"Open Sans",Arial,sans-serif}
  .stage{position:relative;width:1200px;height:780px}
  .card{position:absolute;top:230px;width:540px;height:310px;border-radius:22px;overflow:hidden}
  .card--front{left:40px;background:var(--card-dark)}
  .card--back{left:620px;background:var(--card-light);color:var(--ink)}

  .front-pattern{position:absolute;inset:0;background:linear-gradient(135deg,var(--pattern-a),var(--pattern-b) 55%,var(--pattern-a))}
  .front-brand{position:absolute;left:0;right:0;top:130px;text-align:center;color:var(--white);font-weight:700;font-size:40px;letter-spacing:14px;padding-left:14px}
  .front-brand .mark-dot{display:inline-block;width:14px;height:14px;background:var(--white);border-radius:50%;margin-right:18px;vertical-align:middle;position:relative;top:-4px}

  .back-figure{position:absolute;left:60px;top:40px;width:200px;height:290px;background:linear-gradient(180deg,var(--faint),#efefef);border-radius:90px 90px 0 0}
  .back-name{position:absolute;left:18px;bottom:18px;transform-origin:left bottom;transform:rotate(-90deg) translateY(100%);white-space:nowrap}
  .back-name .person{font-weight:700;font-size:26px;line-height:1.05;display:block}
  .back-name .role{font-size:15px;display:block}

  .back-info{position:absolute;left:285px;top:40px;width:235px}
  .back-brand{font-weight:700;font-size:30px;letter-spacing:9px;color:var(--ink);margin-bottom:22px;display:flex;align-items:center}
  .back-brand .mark-dot{width:12px;height:12px;background:var(--ink);border-radius:50%;margin-right:12px;flex:none}
  .tagline{font-size:13.5px;line-height:1.35;margin-bottom:18px}
  .contact{list-style:none;font-size:13.5px;line-height:1.35}
  .contact li{display:flex;gap:8px;align-items:flex-start;margin-bottom:4px}
  .contact svg{flex:none;margin-top:3px}
</style>
</head>
<body>
<main class="stage">
  <section class="card card--front">
    <div class="front-pattern" role="img" aria-label="Repeating pattern of small brand emblems in dark grey gloss"></div>
    <div class="front-brand"><span class="mark-dot"></span>WALLAY</div>
  </section>

  <section class="card card--back">
    <div class="back-figure" role="img" aria-label="Large faint grey brand emblem in the background"></div>
    <div class="back-name">
      <span class="person">Dalton Pikes</span>
      <span class="role">Founder and CPO</span>
    </div>
    <div class="back-info">
      <div class="back-brand"><span class="mark-dot"></span>WALLAY</div>
      <p class="tagline">If it keeps a drink cold or<br>the party going...we do it!</p>
      <ul class="contact">
        <li>
          <svg width="11" height="11" viewBox="0 0 24 24" aria-hidden="true"><path fill="#111" d="M6.6 10.8a15 15 0 0 0 6.6 6.6l2.2-2.2c.3-.3.7-.4 1-.2 1.1.4 2.3.6 3.6.6.6 0 1 .4 1 1V20c0 .6-.4 1-1 1A17 17 0 0 1 3 4c0-.6.4-1 1-1h3.5c.6 0 1 .4 1 1 0 1.3.2 2.5.6 3.6.1.3 0 .7-.2 1z"/></svg>
          <span>555.318.4726</span>
        </li>
        <li>
          <svg width="11" height="13" viewBox="0 0 24 28" aria-hidden="true"><path fill="none" stroke="#111" stroke-width="2.5" d="M12 26s-8-8.5-8-14a8 8 0 0 1 16 0c0 5.5-8 14-8 14z"/><circle cx="12" cy="12" r="3" fill="#111"/></svg>
          <span>412 E. Carver Avenue,<br>Ste 2207, Tampa, FL. 33917</span>
        </li>
      </ul>
    </div>
  </section>
</main>
</body>
</html>
```